WEBSITE & LOGO for MEDICAL CILINC

BRAND NAME ( LUMORA) Medical clinic for intravenous (IV) vitamin hydration and wellness therapy. range of signature infusions and boosters are targeted at preventative health and wellness – essentially replenishing your body with the fluids and vitamins it needs to be in tip-top condition.

Blood testing
laboratory analysis
IV therapy
IV infusion drips
phlebotomy services
nurses for Home care services
Patient repatriation services to their countries
Hire of medical equipments including beds and wheel chairs

www.quellsa.com
www.tovexclinic.com
http://pickaflask.co.uk

All adults
18+ women and men.

No black color in the background
DNA double helix image should to be implemented in the design and logo.
the website should be easy to be used so the clients can add to the shopping cart
- select treatment or drips
- supplement
- book nurses
- book home visit
- book nurse for international home care journey

Colors
86cae7
33b8a4
e4daeb
f9d9e8
fefafc
fbd2d3
eee9f4
85acd3
0455a3

Requirements
Must have
• DNA Double helix in Java animation
injection icon for IV injection
Infusion Icon Bag for IV infusion
Analysis icon
phlebotomy services icon
Patient repatriation services icon
Hire of medical equipments icon

light background and water blue menu and buttons with highlights
Nice to have
• dynamic website where
IV injections scroll from side to side
IV infusion scroll from side to side.

```html
<!DOCTYPE html>
<html lang="en">
<head>
<meta charset="utf-8">
<title>LUMORA – IV Hydration &amp; Wellness Clinic</title>
<link rel="stylesheet" href="https://fonts.googleapis.com/css2?family=Michroma&family=Rubik:wght@400;500;700&family=Lato:ital,wght@0,400;0,700;1,400&display=swap">
<style>
:root{
  --navy:#06285a;
  --deep:#0a3f8f;
  --blue:#0455a3;
  --sky:#86cae7;
  --teal:#33b8a4;
  --mint:#d6efec;
  --ink:#222a35;
  --grey:#8a8f98;
  --line:#d9dde3;
  --white:#ffffff;
  --footer:#0b2a5c;
}
*{box-sizing:border-box;margin:0;padding:0}
html,body{width:1200px;height:4057px;overflow:hidden;background:var(--white)}
body{position:relative;font-family:'Lato',sans-serif;color:var(--ink)}
.abs{position:absolute}
.btn{position:absolute;display:flex;align-items:center;justify-content:center;gap:8px;font-family:'Rubik',sans-serif;font-weight:500;font-size:14px;color:var(--white);text-transform:uppercase;letter-spacing:.3px}
.btn-teal{background:var(--teal)}
.btn-outline{border:2px solid var(--white)}
.arrow{width:13px;height:13px;border-radius:50%;background:currentColor;position:relative}
.arrow::after{content:"";position:absolute;left:3px;top:4px;width:4px;height:4px;border-top:2px solid var(--teal);border-right:2px solid var(--teal);transform:rotate(45deg)}
.btn-outline .arrow::after,.btn-dark .arrow::after{border-color:var(--blue)}
.btn-dark{background:var(--blue)}

/* header */
.site-header{position:absolute;left:0;top:0;width:1200px;height:103px;background:var(--white)}
.brand{position:absolute;left:143px;top:30px;display:flex;align-items:center;gap:14px}
.brand-mark{width:26px;height:26px;border-radius:50%;background:var(--teal)}
.brand-name{font-family:'Michroma',sans-serif;font-size:34px;color:var(--ink);letter-spacing:2px}
.phone{position:absolute;left:712px;top:4px;display:flex;align-items:center;gap:10px;font-family:'Rubik',sans-serif;font-weight:500;font-size:19px}
.socials-top{position:absolute;left:925px;top:10px;display:flex;gap:6px}
.socials-top span{width:24px;height:24px;border-radius:50%;background:var(--blue)}
.socials-top span:nth-child(2){background:#c8283a}
.socials-top span:nth-child(3){background:#d9453a}
.socials-top span:nth-child(4){background:#b08a4c}
.nav{position:absolute;left:532px;top:64px;display:flex;gap:22px;font-family:'Rubik',sans-serif;font-size:14px;color:#444}
.nav .active{border-bottom:2px solid var(--teal);padding-bottom:7px;color:var(--ink)}
.cart{position:absolute;left:852px;top:58px}

/* hero */
.hero{position:absolute;left:0;top:103px;width:1200px;height:760px;background:linear-gradient(120deg,#0a5fa0 0%,#0a4c8a 40%,#0b3b7c 100%)}
.hero-title{position:absolute;left:143px;top:160px;font-family:'Michroma',sans-serif;font-size:64px;color:var(--white);letter-spacing:3px}
.hero-sub{position:absolute;left:143px;top:270px;width:470px;font-family:'Rubik',sans-serif;font-weight:500;font-size:24px;line-height:36px;color:var(--white)}
.dots{position:absolute;left:1121px;top:253px;display:flex;flex-direction:column;gap:14px}
.dots span{width:7px;height:7px;border-radius:50%;background:var(--white)}
.dots span:nth-child(3){background:var(--teal)}

/* welcome */
.h2{position:absolute;left:0;width:1200px;text-align:center;font-family:'Michroma',sans-serif;font-size:40px;letter-spacing:1px}
.welcome-text{position:absolute;left:190px;top:950px;width:820px;text-align:center;font-size:15px;line-height:34.5px;color:var(--grey)}
.pick{position:absolute;top:1175px;width:190px;text-align:center}
.pick .ring{width:146px;height:146px;margin:0 auto;border-radius:50%;border:3px solid var(--teal);display:flex;align-items:center;justify-content:center;background:var(--white)}
.pick .ring.blue{border-color:var(--blue)}
.pick p{margin-top:14px;font-family:'Rubik',sans-serif;font-weight:500;font-size:14px;line-height:22px;text-transform:uppercase}

/* provide */
.provide{position:absolute;left:0;top:1520px;width:1200px;height:1320px}
.card{position:absolute;width:295px;height:359px;overflow:hidden}
.card .photo{position:absolute;inset:0}
.card h3{position:absolute;left:0;width:100%;top:150px;text-align:center;font-family:'Rubik',sans-serif;font-weight:700;font-size:30px;line-height:32px;color:var(--white);text-transform:uppercase;text-shadow:0 2px 6px rgba(0,0,0,.35)}
.card .btn{left:75px;top:272px;width:145px;height:40px}
.card svg.ic{position:absolute;left:117px;top:40px}

/* testimonials */
.quote{position:absolute;top:3075px;height:180px;background:var(--white);box-shadow:0 3px 10px rgba(0,0,0,.12);text-align:center}
.quote .mark{margin-top:18px;font-family:'Rubik',sans-serif;font-weight:700;font-size:50px;line-height:40px;color:var(--teal)}
.quote p{margin:12px 34px 0;font-style:italic;font-size:12px;line-height:22px;color:var(--grey)}
.quote::after{content:"";position:absolute;left:50%;bottom:-10px;margin-left:-10px;border:10px solid transparent;border-bottom:0;border-top-color:var(--white)}
.author{position:absolute;top:3288px;display:flex;align-items:center;gap:10px}
.author .av{width:42px;height:42px;border-radius:50%;background:linear-gradient(#cdb8a6,#8b7766)}
.author b{display:block;font-family:'Rubik',sans-serif;font-weight:500;font-size:15px;color:var(--ink)}
.author small{font-family:'Rubik',sans-serif;font-size:11px;color:#555}

/* contact */
.contact{position:absolute;left:0;top:3330px;width:1200px;height:660px}
.contact h2{position:absolute;left:165px;top:255px;font-family:'Rubik',sans-serif;font-weight:700;font-size:33px;color:var(--white)}
.field{position:absolute;border:1px solid #6c86ad;font-family:'Rubik',sans-serif;font-size:14px;color:#d9e2ef;padding:14px 25px}
.address{position:absolute;left:782px;top:285px;width:250px;color:var(--white);font-family:'Rubik',sans-serif}
.address h4{font-weight:700;font-size:19px}
.address p{margin-top:12px;font-size:13px;line-height:21px}
.address .tel{display:flex;align-items:center;gap:10px;margin-top:10px;font-size:21px}
.socials-foot{display:flex;gap:11px;margin-top:18px}
.socials-foot span{width:40px;height:40px;border-radius:50%;background:var(--white)}
.footer{position:absolute;left:0;top:3990px;width:1200px;height:67px;background:var(--footer);color:var(--white);font-family:'Rubik',sans-serif;font-size:13px;text-align:center;line-height:67px}
</style>
</head>
<body>

<header class="site-header">
  <div class="brand"><span class="brand-mark"></span><span class="brand-name">LUMORA</span></div>
  <div class="phone">
    <svg width="36" height="36" viewBox="0 0 36 36"><circle cx="18" cy="18" r="16" fill="none" stroke="#86cae7" stroke-width="2.5"/><path d="M12 10l4 0 1.5 4-2.5 2a11 11 0 0 0 5 5l2-2.5 4 1.5v4c-9 1-16-6-14-14z" fill="#86cae7"/></svg>
    1 800 555 0142
  </div>
  <div class="socials-top"><span></span><span></span><span></span><span></span></div>
  <nav class="nav"><span class="active">HOME</span><span>ABOUT</span><span>SERVICES</span><span>CONTACT</span></nav>
  <svg class="cart" width="42" height="34" viewBox="0 0 42 34"><path d="M2 4h7l5 18h20l5-13H12" fill="none" stroke="#33b8a4" stroke-width="3"/><circle cx="16" cy="29" r="3" fill="#33b8a4"/><circle cx="31" cy="29" r="3" fill="#33b8a4"/></svg>
  <div class="btn btn-dark" style="left:927px;top:54px;width:130px;height:39px;font-size:14px;border-radius:2px">Book Online</div>
</header>

<section class="hero">
  <div class="abs" style="inset:0;background:radial-gradient(ellipse at 65% 30%,rgba(70,200,215,.55),rgba(10,60,130,0) 60%)" role="img" aria-label="Glowing turquoise DNA double helix on a deep blue background"></div>
  <h1 class="hero-title">LUMORA</h1>
  <p class="hero-sub">Lorem ipsum dolor sit amet consectetur adipiscing elit sed do eiusmod</p>
  <div class="btn btn-teal" style="left:143px;top:387px;width:166px;height:49px">Book Nurses <span class="arrow"></span></div>
  <div class="btn btn-outline" style="left:319px;top:387px;width:206px;height:49px">Book Home Visit <span class="arrow" style="color:#fff"></span></div>
  <div class="dots"><span></span><span></span><span></span><span></span><span></span></div>
  <svg class="abs" style="left:0;top:520px" width="1200" height="240" viewBox="0 0 1200 240">
    <path d="M0 150 C250 50 450 40 700 130 C900 200 1100 150 1200 50 L1200 240 L0 240Z" fill="#1aa5a5" opacity=".8"/>
    <path d="M0 175 C260 70 460 60 700 145 C900 215 1110 160 1200 75 L1200 240 L0 240Z" fill="#33b8a4"/>
    <path d="M0 205 C260 95 470 80 710 160 C910 230 1120 180 1200 110 L1200 240 L0 240Z" fill="#ffffff"/>
    <path d="M0 240 L0 225 C120 160 200 140 300 130 C180 170 80 200 0 240Z" fill="#ffffff"/>
  </svg>
</section>

<h2 class="h2" style="top:858px">WELCOME TO LUMORA</h2>
<p class="welcome-text">Lorem ipsum dolor sit amet, consectetur adipiscing elit, sed do eiusmod tempor incididunt ut labore et dolore magna aliqua. Ut enim ad minim veniam, quis nostrud exercitation ullamco laboris nisi ut aliquip ex ea commodo consequat. Duis aute irure dolor in reprehenderit in voluptate velit esse cillum dolore eu fugiat nulla parixcepteur sint occaecat cupidatat non proident, sunt in culpa qui officia deserunt mollit anim id est laborum</p>

<div class="pick" style="left:123px"><div class="ring"><svg width="70" height="70" viewBox="0 0 70 70" fill="none" stroke="#222" stroke-width="2.5"><path d="M12 58l10-10M22 48l24-24 6 6-24 24zM46 24l8-8M50 12l8 8"/><rect x="46" y="44" width="14" height="16"/></svg></div><p>Select treatment<br>or drips</p></div>
<div class="pick" style="left:314px"><div class="ring blue"><svg width="70" height="70" viewBox="0 0 70 70" fill="none" stroke="#222" stroke-width="2.5"><rect x="16" y="18" width="30" height="38" rx="3"/><rect x="19" y="10" width="24" height="8"/><path d="M31 29v16M23 37h16"/><rect x="44" y="44" width="18" height="10" rx="5"/></svg></div><p>Supplement</p></div>
<div class="pick" style="left:504px"><div class="ring"><svg width="70" height="70" viewBox="0 0 70 70" fill="none" stroke="#222" stroke-width="2.5"><circle cx="35" cy="26" r="11"/><path d="M24 18h22M35 10v6M32 13h6M14 60c2-12 10-17 21-17s19 5 21 17z"/></svg></div><p>Book nurses</p></div>
<div class="pick" style="left:695px"><div class="ring blue"><svg width="70" height="70" viewBox="0 0 70 70" fill="none" stroke="#222" stroke-width="2.5"><rect x="34" y="8" width="24" height="54"/><circle cx="38" cy="36" r="1.5"/><circle cx="22" cy="24" r="5"/><path d="M15 62V38c0-6 14-6 14 0v24M29 40l5-3"/></svg></div><p>Book home<br>visit</p></div>
<div class="pick" style="left:885px"><div class="ring"><svg width="70" height="70" viewBox="0 0 70 70" fill="none" stroke="#222" stroke-width="2.5"><rect x="10" y="16" width="50" height="32" rx="2"/><path d="M28 56h14M35 48v8M24 32h20M24 38h14"/><circle cx="44" cy="16" r="8"/><path d="M40 16l3 3 5-6"/></svg></div><p>Book nurse for<br>international<br>home care<br>journey</p></div>

<section class="provide">
  <svg class="abs" style="left:0;top:0" width="1200" height="1320" viewBox="0 0 1200 1320" preserveAspectRatio="none">
    <defs><linearGradient id="provideBg" x1="0" y1="0" x2="0" y2="1"><stop offset="0" stop-color="#0a62b0"/><stop offset="1" stop-color="#0a3f96"/></linearGradient></defs>
    <path d="M0 55 C200 -10 420 20 560 55 L0 90Z" fill="#d6efec"/>
    <path d="M560 1262 C750 1215 1000 1200 1200 1235 L1200 1280 C1050 1320 800 1310 560 1262Z" fill="#d6efec"/>
    <path d="M0 55 C250 40 450 100 620 50 C800 0 1000 -20 1200 40 L1200 1225 C1000 1180 800 1200 600 1250 C400 1300 200 1300 0 1275Z" fill="url(#provideBg)"/>
  </svg>
  <h2 class="h2" style="top:180px;color:#fff">WHAT WE PROVIDE</h2>

  <article class="card" style="left:143px;top:297px"><div class="photo" role="img" aria-label="Photo of a gloved hand holding blood sample tubes" style="background:linear-gradient(160deg,#6aa4c8,#2f5e86 60%,#8a3d4a)"></div><div class="photo" style="background:rgba(10,40,80,.25)"></div>
    <svg class="ic" width="60" height="70" viewBox="0 0 60 70" fill="none" stroke="#fff" stroke-width="2.5"><rect x="30" y="4" width="20" height="30" rx="3"/><path d="M8 40h14l6-8h6v24H14zM4 40v20"/></svg>
    <h3>Blood<br>Testing</h3><div class="btn btn-teal">Find More <span class="arrow"></span></div></article>
  <article class="card" style="left:453px;top:297px"><div class="photo" role="img" aria-label="Photo of a lab scientist with safety glasses examining samples" style="background:linear-gradient(160deg,#c8d6e2,#6e90b0 55%,#3d5f88)"></div>
    <svg class="ic" width="60" height="70" viewBox="0 0 60 70" fill="none" stroke="#fff" stroke-width="2.5"><rect x="20" y="4" width="16" height="14"/><path d="M28 18v14M10 40h40v26H10zM18 40v26M30 40v26M42 40v26"/></svg>
    <h3>Laboratory<br>Analysis</h3><div class="btn btn-teal">Find More <span class="arrow"></span></div></article>
  <article class="card" style="left:761px;top:297px"><div class="photo" role="img" aria-label="Photo of a masked nurse preparing an IV bag" style="background:linear-gradient(160deg,#b9c7d4,#7b8ea4 55%,#4f6782)"></div>
    <svg class="ic" width="60" height="70" viewBox="0 0 60 70" fill="none" stroke="#fff" stroke-width="2.5"><rect x="16" y="4" width="28" height="38" rx="8"/><path d="M30 14v14M23 21h14M30 42v10M26 52h8v6h-8zM30 58v8"/></svg>
    <h3>IV<br>Therapy</h3><div class="btn btn-teal">Find More <span class="arrow"></span></div></article>
  <article class="card" style="left:143px;top:670px"><div class="photo" role="img" aria-label="Photo of a patient receiving an IV drip in bed" style="background:linear-gradient(160deg,#e9eef2,#b4c0cc 55%,#8796a6)"></div>
    <svg class="ic" width="60" height="70" viewBox="0 0 60 70" fill="none" stroke="#fff" stroke-width="2.5"><path d="M20 6v60M8 66h44M20 10h16"/><rect x="30" y="12" width="14" height="20" rx="3"/><path d="M37 32v22"/></svg>
    <h3>IV Infusion<br>Drips</h3><div class="btn btn-teal">Find More <span class="arrow"></span></div></article>
  <article class="card" style="left:453px;top:670px"><div class="photo" role="img" aria-label="Photo of a blood draw from a patient's arm" style="background:linear-gradient(160deg,#dce3ea,#a8b6c4 55%,#8c7b78)"></div>
    <svg class="ic" width="60" height="70" viewBox="0 0 60 70" fill="none" stroke="#fff" stroke-width="2.5"><circle cx="30" cy="12" r="8"/><path d="M18 66V30c0-8 24-8 24 0v36"/><circle cx="36" cy="44" r="9"/><path d="M31 49l10-10"/></svg>
    <h3>Phlebotomy<br>Services</h3><div class="btn btn-teal">Find More <span class="arrow"></span></div></article>
  <article class="card" style="left:761px;top:670px"><div class="photo" role="img" aria-label="Photo of a home care nurse with an elderly patient" style="background:linear-gradient(160deg,#c9d4dc,#7fa7a8 55%,#2f8f8a)"></div>
    <svg class="ic" width="60" height="70" viewBox="0 0 60 70" fill="none" stroke="#fff" stroke-width="2.5"><path d="M18 14h24v10H18zM30 16v6M27 19h6"/><circle cx="30" cy="32" r="9"/><path d="M10 66c2-14 10-20 20-20s18 6 20 20z"/></svg>
    <h3>Nurses for<br>Home Care<br>Services</h3><div class="btn btn-teal">Find More <span class="arrow"></span></div></article>

  <div class="btn btn-outline" style="left:474px;top:1085px;width:252px;height:49px">View More Services <span class="arrow" style="color:#fff"></span></div>
</section>

<h2 class="h2" style="top:2955px">WHAT CLIENTS SAY</h2>
<div class="quote" style="left:134px;width:302px"><div class="mark">&ldquo;</div><p>In ullamcorper est eget tempor cursus neque mi consectetuer mi a ultricies massa est sed nisl Class aptent taciti sociosqu ad litora torquent per conubia nostra</p></div>
<div class="quote" style="left:449px;width:305px"><div class="mark">&ldquo;</div><p>In ullamcorper est eget tempor cursus neque mi consectetuer mi a ultricies massa est sed nisl Class aptent taciti sociosqu ad litora torquent per conubia nostra</p></div>
<div class="quote" style="left:770px;width:296px"><div class="mark">&ldquo;</div><p>In ullamcorper est eget tempor cursus neque mi consectetuer mi a ultricies massa est sed nisl Class aptent taciti sociosqu ad litora torquent per conubia nostra</p></div>
<div class="author" style="left:210px"><span class="av" role="img" aria-label="Client portrait"></span><div><b>By Author Name</b><small>City, Location</small></div></div>
<div class="author" style="left:523px"><span class="av" role="img" aria-label="Client portrait"></span><div><b>By Author Name</b><small>City, Location</small></div></div>
<div class="author" style="left:847px"><span class="av" role="img" aria-label="Client portrait"></span><div><b>By Author Name</b><small>City, Location</small></div></div>

<section class="contact">
  <svg class="abs" style="left:0;top:0" width="1200" height="660" viewBox="0 0 1200 660" preserveAspectRatio="none">
    <path d="M0 210 C200 90 450 110 700 170 C900 220 1100 130 1200 20 L1200 660 L0 660Z" fill="#33b8a4"/>
    <path d="M0 215 C210 110 460 130 700 185 C900 235 1100 160 1200 60 L1200 660 L0 660Z" fill="#1f7fae"/>
    <path d="M0 220 C220 125 470 145 700 195 C910 245 1110 180 1200 95 L1200 660 L0 660Z" fill="#06285a"/>
  </svg>
  <h2>CONTACT US</h2>
  <div class="field" style="left:165px;top:322px;width:260px;height:43px">First name</div>
  <div class="field" style="left:434px;top:322px;width:261px;height:43px">Last name</div>
  <div class="field" style="left:165px;top:380px;width:260px;height:43px">Email</div>
  <div class="field" style="left:434px;top:380px;width:261px;height:43px">Phone</div>
  <div class="field" style="left:165px;top:437px;width:530px;height:68px">Message</div>
  <div class="btn btn-teal" style="left:165px;top:523px;width:198px;height:47px;font-size:16px">Submit <span class="arrow"></span></div>
  <div class="address">
    <h4>ADDRESS</h4>
    <p>Lorem Ipsum is simply dummy text of the printing and typesetting industry</p>
    <div class="tel"><svg width="18" height="18" viewBox="0 0 18 18"><path d="M2 2h5l1.5 4-2.5 2a9 9 0 0 0 4 4l2-2.5 4 1.5v5C7 17 1 11 2 2z" fill="#fff"/></svg>1 800 555 0142</div>
    <p>Excepteur sint occaecat cupidatat non mollit anim id est laborum</p>
    <div class="socials-foot"><span></span><span></span><span></span><span></span></div>
  </div>
</section>

<footer class="footer">© 2020 Lumora . All rights reserved | Privacy Policy &nbsp;|&nbsp; Terms and Use</footer>

</body>
</html>
```